Design a New Business Card for Our Company

We are looking for fresh, unique, and a modern business card that reflects our roots as digital marketing agency focused on SEM.

Industry/Entity Type

Marketing

Contact Information for Business Card

looking for very unique out of the box designs. clean and modern that compliments our logo

Requirements
Must have
• colors should match our logo
• Front should have name, address, email, and phone/fax of the person, phone/fax are the same number
• back should have our url

```html
<!DOCTYPE html>
<html lang="en">
<head>
<meta charset="utf-8">
<title>Brightpath Media – Business Card</title>
<link href="https://fonts.googleapis.com/css2?family=Open+Sans:wght@400;600;700&display=swap" rel="stylesheet">
<style>
  :root {
    --bg: #eceae6;
    --brand-blue: #5e98d2;
    --brand-grey: #a9a9a9;
    --paper: #ffffff;
    --paper-shade: #f1f1f1;
    --rule: #c9c9c9;
    --ink-light: #ffffff;
  }
  * { box-sizing: border-box; margin: 0; padding: 0; }
  html, body {
    width: 1200px; height: 900px; overflow: hidden;
    background: var(--bg);
    font-family: "Open Sans", Arial, sans-serif;
  }
  .canvas { position: relative; width: 1200px; height: 900px; }

  .card {
    position: absolute;
    width: 560px; height: 320px;
    border-radius: 4px;
    overflow: hidden;
    box-shadow: 0 6px 18px rgba(0,0,0,0.12);
  }
  .card--back {
    left: 320px; top: 90px; background: var(--brand-blue);
    display: flex; flex-direction: column; align-items: center; justify-content: center; gap: 18px;
  }
  .card--front { left: 320px; top: 490px; background: var(--brand-blue); }

  .wordmark {
    display: flex; align-items: center; gap: 14px;
    font-weight: 700;
    letter-spacing: -1px;
    line-height: 1;
    white-space: nowrap;
  }
  .wordmark__dot { border-radius: 50%; flex: none; }
  .card--back .wordmark { font-size: 44px; color: var(--ink-light); }
  .card--back .wordmark__dot { width: 38px; height: 38px; background: var(--ink-light); }
  .website {
    color: var(--ink-light); font-size: 16px; letter-spacing: 2px; white-space: nowrap;
  }

  .card__top {
    position: absolute; left: 0; top: 0; right: 0; height: 168px;
    background: linear-gradient(180deg, var(--paper) 0%, var(--paper-shade) 100%);
    border-bottom: 5px solid var(--rule);
    display: flex; align-items: center; justify-content: center;
  }
  .card--front .wordmark { font-size: 38px; color: var(--brand-grey); }
  .card--front .wordmark__dot { width: 32px; height: 32px; background: var(--brand-blue); }

  .contact {
    position: absolute; top: 196px; left: 30px; width: 260px;
    color: var(--ink-light); font-size: 15px; text-align: right;
  }
  .contact__row { display: flex; justify-content: flex-end; align-items: center; gap: 8px; height: 27px; white-space: nowrap; }
  .contact__row svg { width: 13px; height: 13px; flex: none; fill: var(--ink-light); }

  .person {
    position: absolute; top: 186px; left: 320px; right: 20px;
    color: var(--ink-light);
  }
  .person__name { font-size: 19px; font-weight: 700; line-height: 1.2; }
  .person__role { font-size: 13px; margin-bottom: 14px; }
  .person__address { font-size: 14px; line-height: 1.35; }
</style>
</head>
<body>
<main class="canvas">
  <section class="card card--back" aria-label="Card back">
    <div class="wordmark"><span class="wordmark__dot"></span><span>brightpath media</span></div>
    <p class="website">www.brightpathmedia.com</p>
  </section>

  <section class="card card--front" aria-label="Card front">
    <div class="card__top">
      <div class="wordmark"><span class="wordmark__dot"></span><span>brightpath media</span></div>
    </div>

    <div class="contact">
      <div class="contact__row"><span>(021)-555-0148</span>
        <svg viewBox="0 0 24 24" aria-hidden="true"><path d="M6.6 10.8a15.1 15.1 0 0 0 6.6 6.6l2.2-2.2c.3-.3.7-.4 1-.2 1.1.4 2.3.6 3.6.6.6 0 1 .4 1 1V20c0 .6-.4 1-1 1A17 17 0 0 1 3 4c0-.6.4-1 1-1h3.5c.6 0 1 .4 1 1 0 1.3.2 2.5.6 3.6.1.3 0 .7-.2 1z"/></svg>
      </div>
      <div class="contact__row"><span>(021)-555-0148</span>
        <svg viewBox="0 0 24 24" aria-hidden="true"><path d="M6 2h10v6H6zM3 9h18v10H3zm3 2v2h2v-2zm4 0v2h2v-2zm4 0v2h4v-2zM6 20h12v2H6z"/></svg>
      </div>
      <div class="contact__row"><span>hello@brightpathmedia.com</span>
        <svg viewBox="0 0 24 24" aria-hidden="true"><path d="M2 5h20v14H2zm2 2v.5l8 5 8-5V7zm0 2.8V17h16V9.8l-8 5z"/></svg>
      </div>
    </div>

    <div class="person">
      <p class="person__name">Daniel Harper</p>
      <p class="person__role">Managing Director</p>
      <p class="person__address">48, Harbour Lane<br>Westford, 40215</p>
    </div>
  </section>
</main>
</body>
</html>
```